KLV Plant Services

We are a heavy diesel mechanical business with additional air con certificates, remapping engine rebuilt

Contact Information for Business Card

Company Name, Director Name, Managing Director, Contact details, email and website

Font styles to use
Serif
Script

```html
<!DOCTYPE html>
<html lang="en">
<head>
<meta charset="utf-8">
<title>KLV Plant Services – Business Card</title>
<link href="https://fonts.googleapis.com/css2?family=Noto+Serif:wght@400;700&display=swap" rel="stylesheet">
<style>
  :root {
    --navy: #25226b;
    --navy-deep: #1f1d5e;
    --ink: #222228;
    --paper: #ffffff;
    --backdrop: #e6e6e9;
  }
  * { box-sizing: border-box; margin: 0; padding: 0; }
  html, body {
    width: 1200px; height: 786px; overflow: hidden;
    background: var(--backdrop);
    font-family: "Noto Serif", Georgia, serif;
  }
  .stage {
    position: relative; width: 1200px; height: 786px;
    display: flex; align-items: center; justify-content: center; gap: 60px;
  }
  .card {
    position: relative; width: 520px; height: 297px; overflow: hidden;
    box-shadow: 0 6px 18px rgba(0,0,0,.18);
  }
  .card-front { background: var(--paper); }
  .card-back { background: var(--navy); display: flex; align-items: center; justify-content: center; }

  .wave { position: absolute; left: 0; bottom: 0; width: 520px; height: 150px; }

  .brand {
    position: absolute; left: 34px; top: 78px; width: 210px;
    display: flex; flex-direction: column; align-items: flex-start;
    color: var(--navy); font-weight: 700;
  }
  .brand-mark { display: flex; align-items: center; gap: 12px; }
  .brand-dot { width: 46px; height: 46px; border-radius: 50%; background: var(--navy); }
  .brand-initials { font-size: 52px; line-height: 1; letter-spacing: 1px; }
  .brand-sub { font-size: 19px; margin-top: 4px; }

  .divider {
    position: absolute; left: 262px; top: 40px; width: 1px; height: 136px; background: var(--navy);
  }

  .contact { position: absolute; left: 282px; top: 34px; color: var(--ink); }
  .person-name { font-size: 19px; font-weight: 700; color: var(--navy); letter-spacing: .5px; line-height: 1.1; }
  .person-role { font-size: 13px; color: var(--navy); margin-bottom: 8px; }
  .contact-list { list-style: none; font-size: 13px; line-height: 1.45; }
  .contact-list li { display: flex; align-items: center; gap: 7px; }
  .contact-list svg { width: 11px; height: 11px; flex: none; fill: var(--navy); }
  .address { font-size: 13px; line-height: 1.4; margin-top: 8px; padding-left: 18px; }

  .back-brand { display: flex; align-items: center; gap: 18px; color: var(--paper); font-weight: 700; }
  .back-dot { width: 70px; height: 70px; border-radius: 50%; background: var(--paper); }
  .back-text { display: flex; flex-direction: column; }
  .back-initials { font-size: 74px; line-height: 1; letter-spacing: 2px; }
  .back-sub { font-size: 27px; margin-top: 4px; }
</style>
</head>
<body>
<main class="stage">

  <section class="card card-front" aria-label="Business card front">
    <div class="brand">
      <div class="brand-mark">
        <span class="brand-dot"></span>
        <span class="brand-initials">KLV</span>
      </div>
      <span class="brand-sub">Plant Services</span>
    </div>

    <div class="divider"></div>

    <div class="contact">
      <p class="person-name">DANIEL HART</p>
      <p class="person-role">Managing Director</p>
      <ul class="contact-list">
        <li>
          <svg viewBox="0 0 24 24" aria-hidden="true"><path d="M6.6 10.8a15 15 0 0 0 6.6 6.6l2.2-2.2a1 1 0 0 1 1-.25 11.4 11.4 0 0 0 3.6.57 1 1 0 0 1 1 1V20a1 1 0 0 1-1 1A17 17 0 0 1 3 4a1 1 0 0 1 1-1h3.5a1 1 0 0 1 1 1c0 1.25.2 2.450.57 3.57a1 1 0 0 1-.25 1z"/></svg>
          123 456 789
        </li>
        <li>
          <svg viewBox="0 0 24 24" aria-hidden="true"><path d="M2 5h20v14H2zm2 2v.5l8 5 8-5V7zm0 2.8V17h16V9.8l-8 5z"/></svg>
          info@yourgmail.com
        </li>
        <li>
          <svg viewBox="0 0 24 24" aria-hidden="true"><path d="M12 2a10 10 0 1 0 0 20 10 10 0 0 0 0-20zm6.9 6h-3a15 15 0 0 0-1.3-3.9A8 8 0 0 1 18.9 8zM12 4c.9 1.2 1.6 2.5 2 4h-4c.4-1.5 1.1-2.8 2-4zM4.3 14a8 8 0 0 1 0-4h3.4a16 16 0 0 0 0 4zm.8 2h3a15 15 0 0 0 1.3 3.9A8 8 0 0 1 5.1 16zm3-8h-3a8 8 0 0 1 4.3-3.9A15 15 0 0 0 8.1 8zM12 20c-.9-1.2-1.6-2.5-2-4h4c-.4 1.5-1.1 2.8-2 4zm2.3-6H9.7a14 14 0 0 1 0-4h4.6a14 14 0 0 1 0 4zm.3 5.9a15 15 0 0 0 1.3-3.9h3a8 8 0 0 1-4.3 3.9zm1.7-5.9a16 16 0 0 0 0-4h3.4a8 8 0 0 1 0 4z"/></svg>
          www.yourwebsite.com
        </li>
      </ul>
      <p class="address">Your address, City<br>State, Zip 1234</p>
    </div>

    <svg class="wave" viewBox="0 0 520 150" preserveAspectRatio="none" aria-hidden="true">
      <path d="M0 130 C 140 124, 280 102, 380 80 C 440 68, 490 62, 520 60 L520 150 L0 150 Z" fill="var(--navy)"/>
      <path d="M0 120 C 140 114, 280 92, 380 70 C 440 58, 490 52, 520 50" fill="none" stroke="var(--navy)" stroke-width="3"/>
    </svg>
  </section>

  <section class="card card-back" aria-label="Business card back">
    <div class="back-brand">
      <span class="back-dot"></span>
      <div class="back-text">
        <span class="back-initials">KLV</span>
        <span class="back-sub">Plant Services</span>
      </div>
    </div>
  </section>

</main>
</body>
</html>
```